Fleyer für Rasenroboter-Garage
Zielgruppe
Aluminiumsysteme
Aufgabenstellung
Für ein neues Produkt " Rasenroboter-Garage" einen Fleyer entwerfen. Format DinA4 Vorder und Rückseite. Bilder der Garage sind als Anhang anbei.Es gibt eine Basic Version mit Dach und eine Expert Version mit Dach und Seitenverkleidung. Sogan " Das Zuhause für Ihren Rasenroboter" . Merkmale sind hochertige Materialien, qualitative Verarbeitung, ästhetisches Design,lange Lebensdauer.

```html
<!DOCTYPE html>
<html lang="de">
<head>
<meta charset="utf-8">
<title>GARAVO – Flyer Rasenroboter-Garage</title>
<link href="https://fonts.googleapis.com/css2?family=Lobster&family=Oswald:wght@400;600&family=Open+Sans:wght@400;600;700&display=swap" rel="stylesheet">
<style>
:root{
  --bg:#e9e6e1;
  --green:#7dbf2a;
  --green-dark:#1f5a24;
  --green-light:#e4f1d3;
  --black:#111;
  --white:#fff;
  --text:#444;
  --sky-top:#3f86d6;
  --sky-low:#cfe3f3;
  --grass:#5ea62a;
}
*{margin:0;padding:0;box-sizing:border-box}
html,body{width:1200px;height:1200px;overflow:hidden;background:var(--bg)}
body{position:relative;font-family:"Open Sans",sans-serif;color:var(--text)}
.page{position:absolute;top:218px;width:540px;height:764px;background:var(--white);overflow:hidden;box-shadow:0 6px 18px rgba(0,0,0,.18)}
.page--front{left:40px}
.page--back{left:620px}
.hero{position:absolute;left:0;top:0;width:540px;background:linear-gradient(to bottom,var(--sky-top) 0%,var(--sky-low) 48%,#9fcf6a 60%,var(--grass) 100%)}
.page--front .hero{height:330px}
.page--back .hero{height:440px}
.photo{position:absolute;background:linear-gradient(160deg,#3d5a48,#1d2e25 60%,#b02a20 61%,#3d5a48 70%);border-radius:2px}
.photo--soft{background:linear-gradient(150deg,#d8dcd8,#4d6b58 45%,#23362b)}
.brand-flag{position:absolute;left:70px;top:0;width:190px;height:150px}
.brand-name{position:absolute;left:94px;top:86px;font-family:"Oswald",sans-serif;font-weight:600;font-size:30px;letter-spacing:1px;color:var(--green)}
.brand-mark{position:absolute;left:94px;top:60px;width:20px;height:20px;background:var(--green)}
.slogan{position:absolute;font-family:"Lobster",sans-serif;color:var(--green-dark);text-shadow:0 0 3px var(--white),0 0 3px var(--white);line-height:1.05}
.slogan--front{left:40px;top:230px;font-size:34px;transform:rotate(-14deg);transform-origin:left top}
.slogan--back{left:30px;top:60px;font-size:40px;transform:rotate(-6deg)}
.price{position:absolute;border-radius:50%;background:var(--green);border:4px solid var(--white);box-shadow:0 2px 6px rgba(0,0,0,.3);color:var(--white);text-align:center;font-family:"Oswald",sans-serif}
.price__value{display:block;font-size:34px;font-weight:600;line-height:1;margin-top:22px}
.price__note{display:block;font-family:"Open Sans",sans-serif;font-size:6px;line-height:1.2;padding:3px 16px 0}
.price--premium{left:395px;top:152px;width:100px;height:100px}
.price--basic{left:430px;top:400px;width:96px;height:96px}
.price--small{left:420px;top:540px;width:96px;height:96px}
.badge-tab{position:absolute;left:402px;top:140px;width:86px;height:20px;background:var(--black);color:var(--white);font-family:"Oswald",sans-serif;font-size:13px;text-align:center;line-height:20px;letter-spacing:1px;z-index:2}
.desc{position:absolute;width:210px}
.desc__title{font-family:"Oswald",sans-serif;font-weight:600;font-size:11px;letter-spacing:1.5px;color:var(--black);margin-bottom:10px}
.desc__label{font-size:8px;font-weight:700;color:var(--green);margin-bottom:2px}
.desc__text{font-size:7.5px;line-height:1.6}
.dims{position:absolute;width:150px;font-size:7.5px;border-collapse:collapse}
.dims caption{text-align:left;font-size:8px;font-weight:700;color:var(--green);padding-bottom:2px}
.dims td{padding:1.5px 4px;border-bottom:1px solid #ddd}
.dims tr:nth-child(odd) td{background:var(--green-light)}
.ticker{position:absolute;left:0;width:540px;height:20px;background:var(--black);color:var(--white);font-family:"Oswald",sans-serif;font-size:10px;letter-spacing:.6px;line-height:20px;text-align:center;white-space:nowrap;overflow:hidden}
.footer{position:absolute;left:0;width:540px;background:var(--green);color:var(--white)}
.page--front .footer{top:680px;height:84px}
.phone{position:absolute;left:40px;top:12px;display:flex;align-items:center;gap:10px;font-family:"Oswald",sans-serif;font-weight:600;font-size:26px;color:var(--black)}
.footer__web{position:absolute;left:40px;top:58px;font-size:8px;font-weight:600;letter-spacing:.5px}
.page--back .footer{top:700px;height:64px}
.address{position:absolute;left:40px;top:22px;font-size:9px;color:var(--black)}
.address strong{font-family:"Oswald",sans-serif;font-weight:600;letter-spacing:.5px}
.benefits{position:absolute;left:330px;top:95px;color:var(--white)}
.benefits__title{font-family:"Oswald",sans-serif;font-size:14px;margin-bottom:8px}
.benefits li{list-style:none;display:flex;align-items:center;gap:8px;font-size:9px;margin-bottom:8px}
</style>
</head>
<body>

<section class="page page--front">
  <div class="hero"></div>
  <div class="photo" style="left:220px;top:190px;width:260px;height:120px" role="img" aria-label="Foto: Rasenroboter-Garagen mit Mähroboter auf blühender Wiese"></div>
  <svg class="brand-flag" viewBox="0 0 190 150"><polygon points="0,0 190,0 190,150 95,120 0,150" fill="#111"/></svg>
  <span class="brand-mark"></span>
  <span class="brand-name">GARAVO</span>
  <div class="badge-tab">PREMIUM</div>
  <div class="price price--premium"><span class="price__value">229,-</span><span class="price__note">mit Seitenwand inkl. MwSt.</span></div>
  <p class="slogan slogan--front">Das Zuhause für<br>Ihren Rasen-Roboter</p>

  <div class="photo photo--soft" style="left:50px;top:380px;width:200px;height:110px" role="img" aria-label="Produktfoto: geschlossene Garage mit Seitenverkleidung"></div>
  <div class="photo photo--soft" style="left:300px;top:345px;width:140px;height:110px" role="img" aria-label="Produktfoto: Garage mit Dach und Mähroboter"></div>
  <div class="price price--basic"><span class="price__value">139,-</span><span class="price__note">inkl. MwSt. zzgl. Versand</span></div>

  <div class="desc" style="left:60px;top:515px">
    <p class="desc__title">PRODUKTBESCHREIBUNG</p>
    <p class="desc__label">MATERIAL:</p>
    <p class="desc__text">Die äußerst stabile Garage ist aus hochwertigem Aluminium gefertigt, der Montage-Befestigungssatz besteht aus rostfreiem Stahl und bietet hervorragenden Schutz gegen - alle Umwelteinflüsse, Ballen-schläge usw...</p>
  </div>
  <table class="dims" style="left:300px;top:500px">
    <caption>ABMESSUNGEN:</caption>
    <tr><td>Höhe</td><td>1445 mm</td></tr>
    <tr><td>Breite</td><td>1525 mm</td></tr>
    <tr><td>Tiefe</td><td>820 mm</td></tr>
    <tr><td>Gewicht</td><td>35 kg</td></tr>
  </table>

  <div class="ticker" style="top:660px">NUR SOLANGE DER VORRAT REICHT +++ BESTELLEN SIE GLEICH HEUTE +++ NUR SOLANGE DER VORRAT REICHT</div>
  <div class="footer">
    <div class="phone">
      <svg width="24" height="24" viewBox="0 0 24 24"><path d="M6.6 10.8a15 15 0 0 0 6.6 6.6l2.2-2.2c.3-.3.7-.4 1-.2 1.1.4 2.3.6 3.6.6.6 0 1 .4 1 1V20c0 .6-.4 1-1 1A17 17 0 0 1 3 4c0-.6.4-1 1-1h3.5c.6 0 1 .4 1 1 0 1.3.2 2.5.6 3.6.1.3 0 .7-.2 1z" fill="#111"/></svg>
      + 49 (0) 321 - 98 76 54 00
    </div>
    <p class="footer__web">WEITERE INFORMATIONEN FINDEN SIE AUF UNSERER WEBSEITE: WWW.GARAVO-BEISPIEL.DE/PROGRAMM</p>
  </div>
</section>

<section class="page page--back">
  <div class="hero"></div>
  <div class="photo" style="left:20px;top:150px;width:170px;height:170px;background:linear-gradient(160deg,#c9753a,#8a4a22)" role="img" aria-label="Foto: Hund in einer Holzhütte auf der Wiese"></div>
  <div class="photo" style="left:290px;top:250px;width:210px;height:120px" role="img" aria-label="Foto: Mähroboter unter einer Garage auf der Wiese"></div>
  <p class="slogan slogan--back">Jeder brauch<br>ein Zuhause!</p>
  <div class="benefits">
    <p class="benefits__title">Ihre Vorteile:</p>
    <ul>
      <li><svg width="10" height="10" viewBox="0 0 10 10"><path d="M1 5l3 3 5-7" stroke="#7dbf2a" stroke-width="2" fill="none"/></svg>stabile Garage</li>
      <li><svg width="10" height="10" viewBox="0 0 10 10"><path d="M1 5l3 3 5-7" stroke="#7dbf2a" stroke-width="2" fill="none"/></svg>aus hochwertigem Aluminium</li>
      <li><svg width="10" height="10" viewBox="0 0 10 10"><path d="M1 5l3 3 5-7" stroke="#7dbf2a" stroke-width="2" fill="none"/></svg>hervorragender Schutz</li>
      <li><svg width="10" height="10" viewBox="0 0 10 10"><path d="M1 5l3 3 5-7" stroke="#7dbf2a" stroke-width="2" fill="none"/></svg>gegen alle Umwelteinflüsse</li>
      <li><svg width="10" height="10" viewBox="0 0 10 10"><path d="M1 5l3 3 5-7" stroke="#7dbf2a" stroke-width="2" fill="none"/></svg>sehr langlebig</li>
    </ul>
  </div>

  <div class="photo photo--soft" style="left:60px;top:420px;width:170px;height:90px" role="img" aria-label="Produktfoto: Garage mit Mähroboter, Seitenansicht"></div>
  <div class="photo photo--soft" style="left:300px;top:410px;width:160px;height:110px" role="img" aria-label="Produktfoto: Garage mit Dach und Mähroboter, Frontansicht"></div>

  <div class="desc" style="left:60px;top:535px">
    <p class="desc__title">PRODUKTBESCHREIBUNG</p>
    <p class="desc__label">MATERIAL:</p>
    <p class="desc__text">Die äußerst stabile Garage ist aus hochwertigem Aluminium gefertigt, der Montage-Befestigungssatz besteht aus rostfreiem Stahl und bietet hervorragenden Schutz gegen - alle Umwelteinflüsse, Ballen-schläge usw...</p>
  </div>
  <table class="dims" style="left:300px;top:560px">
    <caption>ABMESSUNGEN:</caption>
    <tr><td>Höhe</td><td>1445 mm</td></tr>
    <tr><td>Breite</td><td>1525 mm</td></tr>
    <tr><td>Tiefe</td><td>820 mm</td></tr>
    <tr><td>Gewicht</td><td>35 kg</td></tr>
  </table>
  <div class="price price--small"><span class="price__value">79,-</span><span class="price__note">inkl. MwSt. zzgl. Versand</span></div>

  <div class="ticker" style="top:680px">NUR SOLANGE DER VORRAT REICHT +++ BESTELLEN SIE GLEICH HEUTE +++ NUR SOLANGE DER VORRAT REICHT</div>
  <div class="footer">
    <p class="address"><strong>GARAVO</strong> &nbsp;|&nbsp; Beispielweg 7b &nbsp;|&nbsp; 04321 Beispielstadt &nbsp;|&nbsp; E-Mail: info@garavo-beispiel.de</p>
  </div>
</section>

</body>
</html>
```